Advertising company unique advertising platform

we need a logo design for a new company based in Australia Melbourne. We develop innovated advertising platform where consumer can use this platform to get regular discount, as business owner they can use this platform for free advertisement. Payment for this advertisement platform only payable every two weeks, when I generate revenue for their business

Industry/Entity Type

Advertising

Contact Information for Business Card

Dale Morven | Co-Founder |Managing Director
Suite 718 240 Wattlebrook Lane Melbourne Vic 3000

ABN 38 614 207 923
Tel: +61 0487 259 318 | Email: dale.morven@plivorantu.com

Font styles to use
Decorative
Script

Requirements
Must have
• Try few different design and some round corner business card
Should not have
• One round corner business card...try 4 different colour background not only black, make sure two side is designed. Be creative so imagine you are giving this to a client make sure has wow factor, if you can also try one design with engrave like all the logo, words look 3d feel
• The word Advertising Platform use attached file font

```html
<!DOCTYPE html>
<html lang="en">
<head>
<meta charset="UTF-8">
<title>Tallowgrove Business Card</title>
<link href="https://fonts.googleapis.com/css2?family=Marcellus&family=Montserrat:wght@400;500&display=swap" rel="stylesheet">
<style>
  :root {
    --stage: #e9e6e1;
    --card-dark: #2a2a2b;
    --card-dark-2: #1e1e1f;
    --card-light: #ffffff;
    --accent: #f07a22;
    --accent-deep: #e2452a;
    --accent-light: #fbc63c;
    --ink-light: #f2f2f2;
  }
  * { margin: 0; padding: 0; box-sizing: border-box; }
  html, body { width: 1200px; height: 900px; overflow: hidden; }
  body {
    background: var(--stage);
    position: relative;
    font-family: "Montserrat", sans-serif;
  }
  .card {
    position: absolute;
    left: 290px;
    width: 620px;
    height: 354px;
    border-radius: 22px;
    overflow: hidden;
    box-shadow: 0 10px 28px rgba(0,0,0,0.22);
  }
  .card-front {
    top: 70px;
    background: radial-gradient(ellipse at 45% 40%, #3a3a3b 0%, var(--card-dark) 45%, var(--card-dark-2) 100%);
    display: flex;
    align-items: center;
    justify-content: center;
  }
  .brand {
    display: flex;
    align-items: center;
    gap: 16px;
  }
  .brand-dot {
    width: 44px;
    height: 44px;
    border-radius: 50%;
    background: var(--accent);
  }
  .brand-name {
    font-family: "Marcellus", serif;
    color: var(--accent);
    font-size: 48px;
    letter-spacing: 1px;
  }
  .card-back {
    top: 476px;
    background: var(--card-dark);
  }
  .card-back svg.split {
    position: absolute;
    inset: 0;
  }
  .card-back .brand {
    position: absolute;
    right: 30px;
    top: 40px;
    gap: 10px;
  }
  .card-back .brand-dot { width: 28px; height: 28px; }
  .card-back .brand-name { font-size: 30px; }
  .contact {
    position: absolute;
    left: 40px;
    top: 150px;
    color: var(--ink-light);
  }
  .person-name {
    font-family: "Marcellus", serif;
    color: var(--accent);
    font-size: 32px;
    font-weight: 400;
    letter-spacing: 1px;
    line-height: 1;
  }
  .person-role {
    font-family: "Marcellus", serif;
    font-size: 11px;
    letter-spacing: 0.5px;
    margin-top: 4px;
    padding-bottom: 8px;
    border-bottom: 1px solid var(--accent);
    width: 250px;
  }
  .details {
    list-style: none;
    margin-top: 10px;
    font-size: 13.5px;
    line-height: 1.5;
  }
  .details li { display: flex; align-items: center; gap: 8px; }
  .details .icon { width: 11px; height: 11px; flex: none; }
</style>
</head>
<body>
  <section class="card card-front" aria-label="Card front">
    <div class="brand">
      <span class="brand-dot"></span>
      <span class="brand-name">Tallowgrove</span>
    </div>
  </section>

  <section class="card card-back" aria-label="Card back">
    <svg class="split" width="620" height="354" viewBox="0 0 620 354" aria-hidden="true">
      <defs>
        <linearGradient id="swoosh" x1="0" y1="0" x2="0" y2="1">
          <stop offset="0" stop-color="#e2452a"/>
          <stop offset="0.45" stop-color="#fbc63c"/>
          <stop offset="1" stop-color="#e2452a"/>
        </linearGradient>
      </defs>
      <path d="M290 0 C295 60 330 95 400 135 C480 180 560 260 585 354 L620 354 L620 0 Z" fill="#ffffff"/>
      <path d="M290 0 C295 60 330 95 400 135 C480 180 560 260 585 354" fill="none" stroke="url(#swoosh)" stroke-width="9"/>
    </svg>

    <div class="brand">
      <span class="brand-dot"></span>
      <span class="brand-name">Tallowgrove</span>
    </div>

    <div class="contact">
      <h1 class="person-name">DALE MORVEN</h1>
      <p class="person-role">|CO-FOUNDER | MANAGING DIRECTOR</p>
      <ul class="details">
        <li>Suite 718 240 Wattlebrook Lane</li>
        <li>Melbourne Vic 3000</li>
        <li>ABN: 38 614 207 923</li>
        <li>
          <svg class="icon" viewBox="0 0 12 12" aria-hidden="true"><path d="M2.5 1 L4.5 1 L5.2 3.6 L4 4.6 C4.6 6 5.9 7.4 7.4 8 L8.4 6.8 L11 7.5 L11 9.5 C11 10.3 10.3 11 9.5 11 C5 11 1 7 1 2.5 C1 1.7 1.7 1 2.5 1 Z" fill="var(--accent)"/></svg>
          +61 0487 259 318
        </li>
        <li>
          <svg class="icon" viewBox="0 0 12 12" aria-hidden="true"><rect x="1" y="2.5" width="10" height="7" fill="none" stroke="var(--accent)" stroke-width="1.3"/><path d="M1 2.5 L6 6.5 L11 2.5" fill="none" stroke="var(--accent)" stroke-width="1.3"/></svg>
          dale.morven@plivorantu.com
        </li>
      </ul>
    </div>
  </section>
</body>
</html>
```